Edgy book cover - contemporary fiction

A book cover design for a first-time author. The book is being self-published, but needs to stand out as a quality product amongst a huge number of self-published titles hitting the market.

About the book
“Pebbles Under Water” is a collection of eleven fictional short stories, set in the the turbulent economic times of The Great Recession (Or the Global Financial Crisis). The stories are about ordinary people and their struggles and hopes, as they cope with the circumstances that are dealt them: losing their jobs and homes, helping friends in trouble, making their own success, having to move across town or across the world to survive, having to go back to work after losing their retirement savings.

The book is being published as an e-book only at this stage. The graphic will be viewed as an icon on the zorbex lumora store (and similar stores such as Plover vreads), and as a larger image on the book's own page. In future, the cover may be used in a print version.

I expect to be challenged and stimulated along the way as I don’t have a firm view of what the final cover will look like – it really is up to you to wow me. I value your time and as such I will commit to giving each designer feedback.

Required Deliverables

Although you need only submit the book cover at the design stage the required project deliverables are:
- Book Front Cover - colour. Main focus
- Other versions once finalised:
- Colour image image 928px wide by 1250px high, at 150ppi,
- B&W image 96ppi B/W, and it will resize automatically to 600px by 800px, which is perfect for the inside Lumora cover.
- 6 by 4 inch postcards and A4 posters for promotional purposes
- Final tag-line applied to all of the above
- Front, back and spine book cover design for future printing of physical book, size 5.25 inches by 8 inches. Zorbex Pagewell template available when number of pages has been finalised.
- At least 2 iterations of the winning design

Target Market(s)

The target for this book is a broad, educated middle-class audience, say over age 30, for whom home, mortgage and job are real concerns.

Industry/Entity Type

Printing

Requirements
Must have
• The cover needs to be edgy but not overdone. Less is more in this case. Think about the target audience and their tastes. I think the title gives lots of creative possibility, so please be creative and clever. I’d like people to look at the cover and think “Cool/Clever cover – I’d better read this”. Be original yet keep the end product accessible.

There will be a tag-line on the cover somewhere. Where you locate it is up to you, but you need to leave space for it. For the time being please use the text “Songs from Narrow Rooms ” – but this may change by the end of the project.

The following text of title, tagline and author

Pebbles Under Water
Songs from Narrow Rooms
Neil Ashbury

Purely as guidance to my taste, some book covers I like are:

http://lnkmo.example/qa1rt
http://lnkmo.example/k4p2z
http://lnkmo.example/bhe7m
http://lnkmo.example/x9dwo
http://lnkmo.example/r3fuy
http://lnkmo.example/j8cns
Should not have
• Please avoid clichés and being “overly busy”. Although the book is to be self published on a low budget it shouldn’t look like that. If the cover would look right on a popular mass fiction title then it is probably not right for me.

The design should not use a cliched "happy families" house image.

It needs not to look like it's based on a book cover template from a self-publishing house.

Some examples of book covers I don’t like are :

http://lnkmo.example/p2gke
http://lnkmo.example/m7ylh
http://lnkmo.example/t5awq
http://lnkmo.example/f1zbv
http://lnkmo.example/d6oxs

```html
<!DOCTYPE html>
<html lang="en">
<head>
<meta charset="utf-8">
<title>Pebbles Under Water — Neil Ashbury</title>
<link rel="stylesheet" href="https://fonts.googleapis.com/css2?family=Jost:wght@300&display=swap">
<style>
  :root {
    --paper: #ffffff;
    --frame: #3a3a3a;
    --ink: #1b1718;
    --ink-soft: #828282;
    --roof: #d9774a;
    --wall: #b9b3aa;
    --shade: #6f6a62;
    --mint: #8fc7bd;
  }
  html, body {
    margin: 0;
    padding: 0;
    width: 803px;
    height: 1200px;
    overflow: hidden;
    background: var(--paper);
  }
  .cover {
    position: relative;
    width: 803px;
    height: 1200px;
    background: var(--paper);
    font-family: "Jost", "Futura", sans-serif;
    font-weight: 300;
  }
  .cover__frame {
    position: absolute;
    left: 25px;
    top: 25px;
    width: 742px;
    height: 1143px;
    box-sizing: border-box;
    border: 1px solid var(--frame);
  }
  .cover__scene {
    position: absolute;
    left: 0;
    top: 0;
    width: 803px;
    height: 1200px;
  }
  .cover__author {
    position: absolute;
    left: 78px;
    top: 58px;
    margin: 0;
    font-size: 86px;
    line-height: 1;
    letter-spacing: 3px;
    color: var(--ink-soft);
    font-weight: 300;
  }
  .cover__title {
    position: absolute;
    left: 74px;
    top: 150px;
    margin: 0;
    font-size: 128px;
    line-height: 118px;
    letter-spacing: 1px;
    text-transform: uppercase;
    color: var(--ink);
    font-weight: 300;
  }
  .cover__title span { display: block; }
  .cover__tagline {
    position: absolute;
    left: 80px;
    top: 522px;
    margin: 0;
    font-size: 44px;
    line-height: 1;
    color: var(--ink-soft);
    font-weight: 300;
  }
</style>
</head>
<body>
  <main class="cover">
    <svg class="cover__scene" viewBox="0 0 803 1200" role="img" aria-label="Aerial photograph of a street of terraced houses with orange tiled roofs, revealed through a jagged crack in the white cover">
      <defs>
        <linearGradient id="rooftops" x1="1" y1="0" x2="0" y2="1">
          <stop offset="0" stop-color="#8a6a55"/>
          <stop offset="0.3" stop-color="var(--roof)"/>
          <stop offset="0.55" stop-color="var(--wall)"/>
          <stop offset="0.75" stop-color="var(--roof)"/>
          <stop offset="1" stop-color="var(--shade)"/>
        </linearGradient>
      </defs>
      <path fill="url(#rooftops)" d="M767 385 L748 392 L742 410 L712 412 L690 430 L672 462 L660 490 L648 520 L640 548 L618 575 L598 600 L592 640 L572 662 L530 672 L480 690 L445 718 L420 760 L392 790 L352 800 L320 810 L292 826 L290 832 L300 822 L338 826 L345 850 L330 875 L305 915 L288 960 L270 1000 L245 1045 L252 1095 L240 1125 L212 1140 L205 1168 L767 1168 Z"/>
    </svg>
    <div class="cover__frame"></div>
    <p class="cover__author">Neil Ashbury</p>
    <h1 class="cover__title"><span>Pebbles</span><span>Under</span><span>Water</span></h1>
    <p class="cover__tagline">Songs from Narrow Rooms</p>
  </main>
</body>
</html>
```